life insurance quote website design for lepontdoriole.ca

the web site lepontdoriole.ca need a design. we dont like the actuel one but we are open at all new suggestion. visit us at lepontdoriole.ca and you will understand. the principal concurant is tarifsgarantisnord.ca, calculeo.ca, coutprotecfam.ca. We are a life insurance quote site. we found best price available in the canadien industrie. We absolutly want a design with our form in the front page on the top right side like our concurance, we use wordpress at this time. we want to be able to switch language. and to have a logic form. we want to be able to change the color for each type of insurance quote page.we also need a blog in it to post news. and the site will be SEO accurate.

Target Market(s)

Get client fill the quote form

Industry/Entity Type

Insurance

Number of Pages Required

3 page

Font styles to use
Sans Serif

Requirements
Must have
• logic form on the top right first page
• page template for product info stuff, contact, and who we are, blog
• French site
• custum color
Nice to have
• Wordpress design will be appréciate
• switch language english/french

```html
<!DOCTYPE html>
<html lang="fr">
<head>
<meta charset="utf-8">
<title>Le Pont d'Oriole — Soumission d'assurance vie</title>
<link href="https://fonts.googleapis.com/css2?family=Open+Sans:wght@400;600;700;800&display=swap" rel="stylesheet">
<style>
:root{
  --red:#d52027;
  --red-dark:#a3171d;
  --band-top:#7c1418;
  --band-bottom:#9e1c21;
  --blue:#1d7cc4;
  --orange:#f39a1e;
  --green:#3fae49;
  --pink:#e6456a;
  --ink:#2b2b2b;
  --text:#666;
  --muted:#999;
  --line:#e2e2e2;
  --soft:#f1f1f1;
  --footer:#1b1b1b;
  --white:#fff;
}
*{box-sizing:border-box;margin:0;padding:0}
html,body{width:1200px;height:2704px;overflow:hidden}
body{font-family:"Open Sans",Arial,sans-serif;color:var(--text);background:var(--white);position:relative;font-size:13px;line-height:1.6}
.wrap{width:1080px;margin:0 auto;position:relative}

/* header */
.site-header{height:100px;background:var(--white);border-bottom:1px solid var(--line)}
.utility{height:34px;display:flex;justify-content:flex-end;align-items:center;gap:22px;font-size:11px;color:var(--muted);border-bottom:1px solid var(--line)}
.utility span{display:flex;align-items:center;gap:6px}
.nav-row{height:66px;display:flex;align-items:center;justify-content:space-between}
.brand{display:flex;align-items:center;gap:10px;font-weight:800;font-size:20px;color:var(--red)}
.brand .sq{width:22px;height:22px;background:var(--red)}
.main-nav{display:flex;gap:34px;font-size:11px;font-weight:700;text-transform:uppercase;color:var(--ink)}
.main-nav a{text-decoration:none;color:inherit;padding:24px 0}
.main-nav a.active{color:var(--red);border-bottom:3px solid var(--red)}

/* hero */
.hero{height:444px;position:relative}
.hero-photo{position:absolute;inset:0;background:linear-gradient(100deg,#9fbf5a 0%,#c9d98a 30%,#e9dcc4 52%,#d7b79a 70%,#8aa44e 100%)}
.hero-brand{position:absolute;left:60px;top:150px;display:flex;align-items:center;gap:14px;font-weight:800;font-size:34px;color:var(--white)}
.hero-brand .sq{width:40px;height:40px;background:var(--red)}
.hero-panel{position:absolute;right:60px;top:160px;width:300px}
.hero-panel h1{font-size:26px;font-weight:800;color:var(--white);text-transform:uppercase;line-height:1.1}
.hero-panel p{font-size:11px;font-weight:700;color:#fff;background:var(--red);display:inline-block;padding:2px 8px;margin:8px 0 14px;text-transform:uppercase}
.hero-panel .field{height:38px;background:var(--red-dark);color:#f3c5c7;font-size:12px;padding:0 12px;display:flex;align-items:center;margin-bottom:10px}
.hero-panel .btn{height:38px;background:var(--red);color:#fff;font-weight:700;font-size:13px;display:flex;align-items:center;justify-content:center;text-transform:uppercase}

/* promise band */
.promise{height:340px;background:linear-gradient(var(--band-top),var(--band-bottom));text-align:center;color:var(--white)}
.promise h2{padding-top:58px;font-size:24px;font-weight:700;letter-spacing:.5px;text-transform:uppercase}
.promise .rule{width:70px;height:2px;background:#fff;margin:14px auto 40px;opacity:.6}
.features{display:flex;justify-content:space-between;width:900px;margin:0 auto}
.feature{width:200px}
.feature .ico{width:84px;height:84px;border-radius:50%;margin:0 auto 18px;display:flex;align-items:center;justify-content:center;border:4px solid rgba(255,255,255,.25)}
.feature h3{font-size:13px;font-weight:700;text-transform:uppercase}

/* intro + form */
.intro{height:500px;padding-top:60px}
.intro .wrap{display:flex;justify-content:space-between}
.intro-text{width:560px}
.kicker{font-size:14px;font-weight:600;color:var(--ink);text-transform:uppercase}
.intro-text h2{font-size:22px;font-weight:800;color:var(--ink);text-transform:uppercase;margin:2px 0 14px}
.intro-text p{font-size:12px;margin-bottom:12px}
.ticks{list-style:none;margin-top:18px}
.ticks li{font-size:12px;color:var(--red);margin-bottom:8px;display:flex;align-items:center;gap:8px}
.ticks li:nth-child(n+2){color:var(--muted)}
.quote{width:460px;border:1px solid var(--line);box-shadow:0 2px 8px rgba(0,0,0,.08)}
.quote h3{background:var(--blue);color:#fff;text-align:center;font-size:15px;font-weight:600;padding:10px;text-transform:uppercase}
.quote form{padding:14px 18px}
.q-row{display:flex;align-items:center;gap:10px;margin-bottom:10px;font-size:12px;color:var(--ink);font-weight:600}
.q-label{width:90px}
.input{flex:1;height:28px;border:1px solid var(--line);background:#fafafa;font-size:11px;color:var(--muted);padding:0 8px;display:flex;align-items:center;font-weight:400}
.q-title{font-size:12px;font-weight:700;color:var(--ink);margin:4px 0 8px;border-bottom:1px solid var(--line);padding-bottom:4px}
.captcha{width:110px;height:32px;border:1px solid var(--line);font-weight:800;letter-spacing:3px;color:#555;display:flex;align-items:center;justify-content:center;font-size:14px}
.send{background:var(--red);color:#fff;font-weight:700;font-size:13px;padding:8px 20px}

/* how to proceed */
.process{height:460px;background:var(--soft);padding-top:50px}
.process .wrap{display:flex;justify-content:space-between}
.process-text{width:520px}
.process-text h2{font-size:20px;font-weight:800;color:var(--ink);text-transform:uppercase;margin-bottom:12px}
.process-text>p{font-size:12px;margin-bottom:22px}
.steps{display:grid;grid-template-columns:1fr 1fr;gap:20px 28px}
.step h4{display:flex;align-items:center;gap:8px;font-size:13px;color:var(--ink);font-weight:700;margin-bottom:4px}
.step h4 i{width:22px;height:22px;border-radius:50%;background:var(--red);display:inline-block}
.step p{font-size:11px;line-height:1.5}
.video{width:520px;height:340px;position:relative;background:linear-gradient(135deg,#b8b2a8,#e2ddd3 45%,#8d8478);}
.video-label{position:absolute;left:50%;top:50%;transform:translate(-50%,-50%);display:flex;align-items:center;gap:14px;color:#fff;font-size:24px;font-weight:700;letter-spacing:1px}
.play{width:70px;height:70px;border-radius:50%;border:3px solid #fff;display:flex;align-items:center;justify-content:center}

/* blog */
.blog{height:520px;padding-top:44px}
.blog h2{text-align:center;font-size:26px;font-weight:600;color:var(--ink)}
.blog .rule{width:60px;height:2px;background:var(--red);margin:10px auto 34px}
.cards{display:flex;justify-content:space-between}
.card{width:255px;box-shadow:0 1px 6px rgba(0,0,0,.12)}
.card .img{height:160px}
.card .body{padding:14px}
.card h3{font-size:13px;font-weight:700;color:var(--ink);text-transform:uppercase;margin-bottom:6px}
.card p{font-size:11px;line-height:1.5;margin-bottom:10px}
.meta{display:flex;gap:14px;font-size:10px;color:var(--muted);border-top:1px solid var(--line);padding-top:8px}
.meta span{display:flex;align-items:center;gap:5px}
.meta i{width:8px;height:8px;background:var(--red);border-radius:50%;display:inline-block}

/* footer */
.site-footer{height:296px;background:var(--footer);color:#aaa;padding-top:50px}
.site-footer .wrap{display:flex;justify-content:space-between}
.f-col h4{color:#fff;font-size:13px;font-weight:700;text-transform:uppercase;margin-bottom:14px}
.f-col p{font-size:11px;line-height:1.8}
.badge{width:150px;height:70px;background:#2c2c2c;border:1px solid #3a3a3a}
.news-in{display:flex;margin-top:12px}
.news-in .input{background:#2c2c2c;border:none;height:30px;width:190px;flex:none}
.news-in .go{background:var(--red);color:#fff;font-size:11px;font-weight:700;padding:0 16px;display:flex;align-items:center}
.social{display:flex;gap:8px;margin-top:14px;justify-content:center}
.social i{width:26px;height:26px;border-radius:50%;border:1px solid #666;display:inline-block}
.copyright{position:absolute;left:0;right:0;bottom:0;height:44px;background:var(--red);color:#fff;font-size:11px;display:flex;align-items:center;justify-content:center}
.copyright .top{position:absolute;right:60px}
</style>
</head>
<body>

<header class="site-header">
  <div class="wrap">
    <div class="utility">
      <span>☎ 1 800 555-0142</span>
      <span>✉ info@lepontdoriole.ca</span>
      <span>FR | EN</span>
      <span>Connexion</span>
    </div>
    <div class="nav-row">
      <div class="brand"><span class="sq"></span>Le Pont d'Oriole</div>
      <nav class="main-nav">
        <a class="active" href="#">Home</a>
        <a href="#">Products</a>
        <a href="#">Submission</a>
        <a href="#">Who we are</a>
        <a href="#">Contact us</a>
      </nav>
    </div>
  </div>
</header>

<section class="hero">
  <div class="hero-photo" role="img" aria-label="Smiling family of four lying together on green grass outdoors"></div>
  <div class="hero-brand"><span class="sq"></span>Le Pont d'Oriole</div>
  <div class="hero-panel">
    <h1>Le Pont d'Oriole</h1>
    <p>Online life insurance submission</p>
    <div class="field">Enter the name</div>
    <div class="btn">Log in</div>
  </div>
</section>

<section class="promise">
  <h2>The assurance of getting the best price</h2>
  <div class="rule"></div>
  <div class="features">
    <div class="feature">
      <div class="ico" style="background:var(--blue)"><svg width="38" height="38" viewBox="0 0 24 24" fill="#fff"><path d="M12 2C6.5 2 2 6 2 11h20c0-5-4.5-9-10-9z"/><rect x="11.2" y="11" width="1.6" height="8"/><path d="M12.8 19a2.5 2.5 0 0 1-5 0h1.6a.9.9 0 0 0 1.8 0z"/></svg></div>
      <h3>Life insurance</h3>
    </div>
    <div class="feature">
      <div class="ico" style="background:var(--orange)"><svg width="38" height="38" viewBox="0 0 24 24" fill="none" stroke="#fff" stroke-width="2.2" stroke-linecap="round"><path d="M12 3v18M16.5 7.5c-.8-1.3-2.5-2-4.5-2-2.5 0-4 1.3-4 3s1.5 2.6 4 3.2 4.5 1.4 4.5 3.3-1.8 3.3-4.5 3.3c-2.2 0-4-.9-4.8-2.3"/></svg></div>
      <h3>Salary</h3>
    </div>
    <div class="feature">
      <div class="ico" style="background:var(--green)"><svg width="38" height="38" viewBox="0 0 24 24" fill="#fff"><path d="M12 3 2 11h3v10h5v-6h4v6h5V11h3z"/></svg></div>
      <h3>Mortgage</h3>
    </div>
    <div class="feature">
      <div class="ico" style="background:var(--pink)"><svg width="38" height="38" viewBox="0 0 24 24" fill="#fff"><path d="M12 21s-8-5.3-8-11a4.5 4.5 0 0 1 8-2.8A4.5 4.5 0 0 1 20 10c0 5.7-8 11-8 11z"/></svg></div>
      <h3>Serious diseases</h3>
    </div>
  </div>
</section>

<section class="intro">
  <div class="wrap">
    <div class="intro-text">
      <div class="kicker">Online life insurance submission</div>
      <h2>Find the best insurance at the best price!</h2>
      <p>Whether you are buying life insurance, mortgage insurance or disability coverage, our team compares the offers of the leading Canadian insurers to bring you the lowest premium available. Fill in our short form and receive your personalized quotes within minutes, free of charge and with no obligation.</p>
      <p>For more than ten years, our brokers have helped thousands of families protect what matters most. We explain every option in plain words so that you can choose the coverage that fits your budget, your family and your future plans with complete confidence.</p>
      <ul class="ticks">
        <li><svg width="10" height="10" viewBox="0 0 10 10"><path d="M2 1l5 4-5 4z" fill="currentColor"/></svg>Permanent life insurance – term life insurance</li>
        <li><svg width="10" height="10" viewBox="0 0 10 10"><path d="M2 1l5 4-5 4z" fill="currentColor"/></svg>Disability insurance – disability coverage</li>
        <li><svg width="10" height="10" viewBox="0 0 10 10"><path d="M2 1l5 4-5 4z" fill="currentColor"/></svg>Mortgage insurance – loans</li>
        <li><svg width="10" height="10" viewBox="0 0 10 10"><path d="M2 1l5 4-5 4z" fill="currentColor"/></svg>Critical illness insurance</li>
      </ul>
    </div>
    <div class="quote">
      <h3>Quote request</h3>
      <form>
        <div class="q-row"><span class="q-label">Products</span><span class="input">Select a product ▾</span></div>
        <div class="q-title">Applicant</div>
        <div class="q-row"><span class="input">First name</span><span class="input">Last name</span></div>
        <div class="q-row"><span class="input">Gender ▾</span><span class="input">Smoker ▾</span></div>
        <div class="q-row"><span class="input">Day ▾</span><span class="input">Month ▾</span><span class="input">Year ▾</span></div>
        <div class="q-row"><span class="input">Coverage amount</span><span class="input">Term ▾</span></div>
        <div class="q-row"><span class="q-label">Co-Applicant</span><span style="font-weight:400">◯ Yes &nbsp; ◉ No</span></div>
        <div class="q-row"><span class="input">Email</span><span class="input">Phone</span></div>
        <div class="q-row"><span class="input">Postal code</span><span class="captcha">DBLKL</span></div>
        <div class="q-row" style="justify-content:flex-end;margin:0"><span class="send">Send Now</span></div>
      </form>
    </div>
  </div>
</section>

<section class="process">
  <div class="wrap">
    <div class="process-text">
      <div class="kicker">How to proceed?</div>
      <h2>The online life insurance submission</h2>
      <p>Getting the right protection is simple. Complete our secure form, compare the offers we find for you and choose the plan that suits your needs. One of our licensed advisors will then guide you until your policy is issued.</p>
      <div class="steps">
        <div class="step"><h4><i></i>Financial advisors Security</h4><p>Our licensed advisors protect your data and answer all your questions at every step of the process.</p></div>
        <div class="step"><h4><i></i>Insurance ?</h4><p>We compare premiums from many insurers so you never pay more than the best price available.</p></div>
        <div class="step"><h4><i></i>Not Annoying</h4><p>No endless calls or pressure. We contact you only when you ask us to, by phone or by email.</p></div>
        <div class="step"><h4><i></i>Free to Ask</h4><p>Our quotes are free and without obligation. Ask as many questions as you like before deciding.</p></div>
      </div>
    </div>
    <div class="video" role="img" aria-label="Advisor meeting with a couple at a table in a bright office">
      <div class="video-label">OUR <span class="play"><svg width="22" height="22" viewBox="0 0 10 10"><path d="M2 1l7 4-7 4z" fill="#fff"/></svg></span> VIDEOS</div>
    </div>
  </div>
</section>

<section class="blog">
  <h2>Our Blog</h2>
  <div class="rule"></div>
  <div class="wrap cards">
    <article class="card">
      <div class="img" role="img" aria-label="Family relaxing together on a sofa at home" style="background:linear-gradient(135deg,#d8c3a8,#a88766)"></div>
      <div class="body"><h3>Permanent life</h3><p>Whether you are looking for life insurance, mortgage coverage or a plan for your family, learn how to pay the right amount.</p><div class="meta"><span><i></i>Jan. 2016</span><span><i></i>3 Comments</span></div></div>
    </article>
    <article class="card">
      <div class="img" role="img" aria-label="Parents and child reading together indoors" style="background:linear-gradient(135deg,#e8d6c0,#b79c7c)"></div>
      <div class="body"><h3>Permanent life</h3><p>Whether you are looking for life insurance, mortgage coverage or a plan for your family, learn how to pay the right amount.</p><div class="meta"><span><i></i>Jan. 2016</span><span><i></i>3 Comments</span></div></div>
    </article>
    <article class="card">
      <div class="img" role="img" aria-label="Family walking on a beach at sunset" style="background:linear-gradient(180deg,#5d8fc9,#f0b25c)"></div>
      <div class="body"><h3>Permanent life</h3><p>Whether you are looking for life insurance, mortgage coverage or a plan for your family, learn how to pay the right amount.</p><div class="meta"><span><i></i>Jan. 2016</span><span><i></i>3 Comments</span></div></div>
    </article>
    <article class="card">
      <div class="img" role="img" aria-label="Couple signing documents with an advisor" style="background:linear-gradient(135deg,#c9cfd6,#7e8a96)"></div>
      <div class="body"><h3>Permanent life</h3><p>Whether you are looking for life insurance, mortgage coverage or a plan for your family, learn how to pay the right amount.</p><div class="meta"><span><i></i>Jan. 2016</span><span><i></i>3 Comments</span></div></div>
    </article>
  </div>
</section>

<footer class="site-footer">
  <div class="wrap">
    <div class="f-col"><div class="badge"></div></div>
    <div class="f-col">
      <h4>Our Offices</h4>
      <p>Head Office : 1200 Rue des Érables<br>Québec QC, G1R 0A4<br>Phone : 1 800 555-0142<br>Fax : 1 800 555-0143<br>Email : info@lepontdoriole.ca</p>
    </div>
    <div class="f-col">
      <h4>Hours of Operation</h4>
      <p>Our hours of operation<br>Monday to Friday: 9 am to 5 pm<br>Sunday : Closed all day</p>
    </div>
    <div class="f-col" style="width:260px">
      <h4>Newsletter</h4>
      <p>Get our latest news, tips and advice on life insurance sent straight to your inbox.</p>
      <div class="news-in"><span class="input">Your email</span><span class="go">Send</span></div>
      <div class="social"><i></i><i></i><i></i></div>
    </div>
  </div>
  <div class="copyright">Copyright@2016 Le Pont d'Oriole. All rights reserved<span class="top">TOP</span></div>
</footer>

</body>
</html>
```